2 Flow Charts showing Fair Trade vs Market Trade****See new image*****

I am starting a coffee roasting company where I warehouse coffee for farmers I met in Nicaragua as a Harbor League Volunteer.

I need one flow chart to show the normal path of coffee, from the producer to the exporter, to the importer, to the roaster, and ultimately to the consumer, each of which taking a little along the way, leaving the farmer less.

Then another flow chart showing a close relationship between my company (Brass Lantern Coffee) and the producer, with out the exporter/importer, and more money going to the farmer.

I have included my attempt at the flow charts, which look clunky and are in super low res.

You can see how I want to use the flow charts in the following website:

brasslanterncoffeeroasters.example

****** Just reduced the verbiage on the Flow Charts****************
***************See new image*******************************

Target Market(s)

Coffee consumers interested in fair trade.

Industry/Entity Type

It Company

Font styles to use
Sans Serif

Requirements
Must have
• Originally thinking black and white, but am open to color.
Nice to have
• Would like to see a design in both color and monochrome. I am having a difficult time determining which would look better on the site.

```html
<!DOCTYPE html>
<html lang="en">
<head>
<meta charset="utf-8">
<title>The Brass Lantern Model</title>
<link rel="stylesheet" href="https://fonts.googleapis.com/css2?family=Jost:wght@500;600;700;800&display=swap">
<style>
  :root {
    --blue: #3a86cf;
    --red: #f0502a;
    --blush: #f8c9b8;
    --bean: #8a5a45;
    --paper: #ffffff;
  }
  html, body {
    margin: 0;
    padding: 0;
    overflow: hidden;
    background: var(--paper);
  }
  .canvas {
    position: relative;
    width: 1200px;
    height: 1000px;
    overflow: hidden;
    background: var(--paper);
    font-family: "Jost", "Futura", sans-serif;
  }
  .model-chart { position: absolute; left: 0; top: 0; }
  .title { font-size: 42px; font-weight: 800; fill: var(--blue); }
  .tagline { font-size: 17px; font-weight: 600; fill: var(--blue); }
  .bracket { fill: none; stroke: var(--red); stroke-width: 2.5; }
  .badge-box { fill: var(--blue); }
  .badge-text { font-size: 18px; font-weight: 800; fill: #fff; }
  .stage-big { font-size: 18px; font-weight: 800; fill: var(--blue); }
  .stage-small { font-size: 11px; font-weight: 800; fill: var(--blue); }
  .stage-brand { font-size: 11px; font-weight: 800; fill: var(--blue); }
  .coffee-label { font-size: 15px; font-weight: 800; fill: var(--red); }
  .icon { fill: none; stroke: var(--blue); stroke-width: 2.5; stroke-linejoin: round; stroke-linecap: round; }
  .icon-fill { fill: var(--blue); }
  .producer-mark { fill: var(--blue); opacity: .85; }
  .brand-square { fill: var(--red); }
  .track { stroke: var(--blue); stroke-width: 2.5; fill: none; }
  .flow { stroke: var(--red); stroke-width: 2.5; fill: none; }
  .flow-head { fill: var(--red); }
  .bean { fill: var(--bean); }
  .money { stroke: var(--blush); stroke-width: 2; fill: none; }
  .money-text { font-size: 15px; font-weight: 700; fill: var(--blush); }
  .node { fill: #fff; stroke: var(--red); stroke-width: 2.5; }
  .node-hot { fill: var(--red); stroke: var(--blue); stroke-width: 2; }
  .node-num { font-size: 10px; font-weight: 800; fill: var(--blue); }
  .node-num-hot { font-size: 10px; font-weight: 800; fill: #fff; }
  .dollars { font-size: 24px; font-weight: 800; fill: var(--blue); }
  .caption { font-size: 15px; font-weight: 500; fill: var(--blue); }
  .caption strong, .caption .em { font-weight: 700; }
  .rise { stroke: var(--blue); stroke-width: 2.5; fill: none; }
  .rise-head { fill: var(--blue); }
</style>
</head>
<body>
<div class="canvas">
<svg class="model-chart" width="1200" height="1000" viewBox="0 0 1200 1000" xmlns="http://www.w3.org/2000/svg">
  <defs>
    <g id="cup">
      <path class="icon" d="M-22 -14 H16 V8 Q16 22 -3 22 Q-22 22 -22 8 Z"/>
      <path class="icon" d="M16 -8 Q28 -8 28 2 Q28 12 15 12"/>
      <ellipse class="bean" cx="-3" cy="4" rx="8" ry="11" transform="rotate(25 -3 4)"/>
      <path d="M-8 12 Q-3 4 2 -4" stroke="#fff" stroke-width="1.5" fill="none"/>
      <path class="icon" stroke-width="2" d="M-6 -20 q-4 -4 0 -8 q4 -4 0 -8 M0 -20 q-4 -4 0 -8 q4 -4 0 -8"/>
    </g>
    <g id="bean-dot">
      <ellipse class="bean" cx="0" cy="0" rx="4" ry="6" transform="rotate(30)"/>
    </g>
  </defs>

  <!-- Heading -->
  <text class="title" x="620" y="343" text-anchor="middle">THE BRASS LANTERN MODEL</text>
  <path class="bracket" d="M272 353 H265 V383 H272"/>
  <path class="bracket" d="M966 353 H973 V383 H966"/>
  <text class="tagline" x="619" y="375" text-anchor="middle">We do things differently. We do away with the middlemen and give more to the farmers.</text>

  <!-- Traditional trade -->
  <g class="traditional-trade">
    <rect class="badge-box" x="178" y="410" width="192" height="27"/>
    <text class="badge-text" x="274" y="430" text-anchor="middle">TRADITIONAL TRADE</text>

    <!-- producer -->
    <rect class="producer-mark" x="40" y="462" width="26" height="50" rx="6" role="img" aria-label="Producer icon: coffee farmer in a hat"/>
    <!-- exporter warehouse -->
    <g transform="translate(166 497)">
      <path class="icon" d="M-26 16 V-4 Q-26 -22 -6 -22 Q14 -22 14 -4 V16 Z"/>
      <path class="icon" d="M-18 -22 Q-2 -28 10 -20 Q22 -12 22 4 V16 H14"/>
      <rect class="icon" x="-16" y="2" width="20" height="14"/>
      <path class="icon" stroke-width="1.5" d="M-16 7 H4 M-16 11 H4"/>
    </g>
    <!-- importer -->
    <path class="icon" d="M242 513 V494 L257 483 L272 494 V513 Z M252 513 V503 H262 V513"/>
    <!-- roaster -->
    <path class="icon" d="M324 495 L348 477 L372 495 M331 490 V513 H365 V490 M343 513 V502 H353 V513"/>
    <!-- cup -->
    <use href="#cup" x="480" y="495"/>

    <!-- forward arrows -->
    <g>
      <path class="flow" d="M74 497 H126"/><path class="flow-head" d="M134 497 L126 493 V501 Z"/><use href="#bean-dot" x="100" y="497"/>
      <path class="flow" d="M198 497 H228"/><path class="flow-head" d="M235 497 L227 493 V501 Z"/><use href="#bean-dot" x="213" y="497"/>
      <path class="flow" d="M283 497 H310"/><path class="flow-head" d="M317 497 L309 493 V501 Z"/><use href="#bean-dot" x="298" y="497"/>
      <path class="flow" d="M380 497 H436"/><path class="flow-head" d="M444 497 L436 493 V501 Z"/><use href="#bean-dot" x="410" y="497"/>
    </g>

    <text class="stage-big" x="53" y="537" text-anchor="middle">PRODUCER</text>
    <text class="stage-small" x="166" y="535" text-anchor="middle">EXPORTER</text>
    <text class="stage-small" x="257" y="535" text-anchor="middle">IMPORTER</text>
    <text class="stage-small" x="348" y="535" text-anchor="middle">COFFEE ROASTER</text>
    <text class="stage-big" x="483" y="537" text-anchor="middle">YOUR COFFEE</text>

    <path class="track" d="M55 552 H482"/>
    <circle class="node-hot" cx="55" cy="552" r="8"/><text class="node-num-hot" x="55" y="556" text-anchor="middle">1</text>
    <circle class="node" cx="167" cy="552" r="8"/><text class="node-num" x="167" y="556" text-anchor="middle">2</text>
    <circle class="node" cx="258" cy="552" r="8"/><text class="node-num" x="258" y="556" text-anchor="middle">3</text>
    <circle class="node" cx="348" cy="552" r="8"/><text class="node-num" x="348" y="556" text-anchor="middle">4</text>
    <circle class="node-hot" cx="482" cy="552" r="8"/><text class="node-num-hot" x="482" y="556" text-anchor="middle">5</text>

    <g>
      <text class="money-text" x="80" y="571">←</text><text class="money-text" x="97" y="571">$</text><path class="money" d="M110 566 H133"/>
      <text class="money-text" x="180" y="571">←$$</text><path class="money" d="M219 566 H241"/>
      <text class="money-text" x="270" y="571">←$$$</text><path class="money" d="M318 566 H335"/>
      <text class="money-text" x="378" y="571">←$$$$</text><path class="money" d="M436 566 H452"/>
    </g>

    <text class="caption" x="273" y="611" text-anchor="middle">Traditionally, farmers sell their coffee for</text>
    <text class="caption" x="273" y="631" text-anchor="middle" font-weight="700">1$ to $1.85 a pound</text>
  </g>

  <!-- Brass Lantern trade -->
  <g class="direct-trade">
    <rect class="badge-box" x="860" y="410" width="212" height="27"/>
    <text class="badge-text" x="966" y="430" text-anchor="middle">BRASS LANTERN TRADE</text>

    <rect class="producer-mark" x="823" y="456" width="26" height="46" rx="6" role="img" aria-label="Producer icon: coffee farmer in a hat"/>
    <rect class="brand-square" x="1071" y="462" width="44" height="44"/>

    <text class="caption" x="960" y="481" text-anchor="middle">We directly import</text>
    <text class="caption" x="960" y="499" text-anchor="middle">and roast the coffee</text>

    <text class="stage-small" x="836" y="520" text-anchor="middle">PRODUCER</text>
    <text class="stage-brand" x="1093" y="520" text-anchor="middle">BRASS LANTERN</text>

    <path class="flow" d="M878 518 H1040"/><path class="flow-head" d="M1048 518 L1040 514 V522 Z"/><use href="#bean-dot" x="967" y="518"/>

    <path class="track" d="M836 535 H1093"/>
    <circle class="node" cx="836" cy="535" r="8"/><text class="node-num" x="836" y="539" text-anchor="middle">1</text>
    <circle class="node" cx="1093" cy="535" r="8"/><text class="node-num" x="1093" y="539" text-anchor="middle">1</text>

    <text class="money-text" x="880" y="554">←</text><path class="money" d="M896 549 H958"/>
    <text class="money-text" x="963" y="554">$</text><path class="money" d="M976 549 H1050"/>

    <path class="rise" d="M836 660 V560"/><path class="rise-head" d="M836 552 L831 561 H841 Z"/>
    <path class="rise" d="M1093 660 V560"/><path class="rise-head" d="M1093 552 L1088 561 H1098 Z"/>
    <text class="dollars" x="836" y="618" text-anchor="middle" style="paint-order:stroke" stroke="#fff" stroke-width="10">$$</text>
    <text class="dollars" x="1093" y="618" text-anchor="middle" style="paint-order:stroke" stroke="#fff" stroke-width="10">$$</text>

    <use href="#cup" x="968" y="605"/>
    <text class="coffee-label" x="963" y="644" text-anchor="middle">YOUR COFFEE</text>

    <path class="track" d="M836 660 H1093"/>
    <circle class="node-hot" cx="963" cy="660" r="8"/><text class="node-num-hot" x="963" y="664" text-anchor="middle">2</text>

    <text class="caption" x="963" y="688" text-anchor="middle">We share revenues, guaranteeing</text>
    <text class="caption" x="963" y="707" text-anchor="middle">our farmers <tspan font-weight="700">$3.25 a pound</tspan></text>
  </g>
</svg>
</div>
</body>
</html>
```